Korval Advise Business Cards

We need a business card design for Korval Advise (Logo Attached), a management consultancy specialized in brand & business building.

Design should be clean, smart and a touch of innnovation without being gimmicky.

The details on the card should be:
Name: Tomas Velduren
Title: Managing Director
Address: 42 Marlowe Pier, Tarn Vessel Tower, Singapore 073926
Tel: +6285927461082
email: tv@korvaladvise.example
website: korvaladvise.example

For further background on corporate identity, please check www.korvaladvise.example
Updates

Dear all,

Many thanks for the submissions so far! I gave feedback to those designs that I prefer at this stage.

Overall I see that my preference goes into the direction that 'less is more' and 'simple is beautiful'

Please create uniqueness and standout by the simplicity and attraction of the overall concept and design.

Many thanks and please shout incase of questions!

Tomas

Industry/Entity Type

Business

```html
<!DOCTYPE html>
<html lang="en">
<head>
<meta charset="utf-8">
<title>Korval Advise Business Cards</title>
<link rel="stylesheet" href="https://fonts.googleapis.com/css2?family=Open+Sans:wght@400;600;700&display=swap">
<style>
  :root {
    --page: #ecebe8;
    --card-white: #ffffff;
    --charcoal: #4a4a4a;
    --ink: #3f3f3f;
    --orange: #f26b1d;
    --white: #ffffff;
  }
  * { box-sizing: border-box; margin: 0; padding: 0; }
  html, body {
    width: 1174px; height: 1200px; overflow: hidden;
    background: var(--page);
    font-family: "Open Sans", Arial, sans-serif;
  }
  .canvas { position: relative; width: 1174px; height: 1200px; }

  .card { position: absolute; width: 942px; height: 537px; }
  .card--front { left: 22px; top: 42px; background: var(--card-white); box-shadow: 0 2px 8px rgba(0,0,0,.15); }
  .card--back { left: 207px; top: 614px; background: var(--charcoal); box-shadow: 0 2px 8px rgba(0,0,0,.2); }

  .company-name { position: absolute; font-weight: 600; white-space: nowrap; letter-spacing: -0.5px; line-height: 1; }
  .card--front .company-name { left: 33px; top: 72px; font-size: 74px; color: var(--ink); }
  .card--back .company-name { left: 0; right: 0; top: 218px; text-align: center; font-size: 90px; color: var(--white); }

  .side-tab { position: absolute; }
  .side-tab--left { left: 0; top: 293px; width: 17px; height: 210px; background: var(--charcoal); border-radius: 0 10px 10px 0; }
  .side-tab--right { right: 0; top: 360px; width: 17px; height: 80px; background: var(--orange); border-radius: 10px 0 0 10px; }

  .contact { position: absolute; left: 33px; top: 300px; font-size: 22px; color: var(--ink); line-height: 1; }
  .contact__row { display: flex; align-items: center; gap: 8px; height: 40px; }
  .contact__icon { width: 22px; height: 22px; flex: none; }
  .contact__address { margin-top: 14px; line-height: 33px; }

  .person { position: absolute; right: 30px; top: 364px; text-align: right; }
  .person__name { font-size: 27px; font-weight: 700; color: var(--ink); line-height: 36px; }
  .person__title { font-size: 22px; color: var(--orange); line-height: 30px; }

  .back-url { position: absolute; left: 0; right: 0; top: 412px; text-align: center; color: var(--white); font-size: 23px; letter-spacing: 5px; }
</style>
</head>
<body>
<main class="canvas">
  <section class="card card--front" aria-label="Card front">
    <div class="company-name">Korval Advise</div>
    <div class="side-tab side-tab--left"></div>
    <div class="side-tab side-tab--right"></div>
    <div class="contact">
      <div class="contact__row">
        <svg class="contact__icon" viewBox="0 0 22 22" aria-hidden="true"><circle cx="11" cy="11" r="10" fill="none" stroke="var(--orange)" stroke-width="2"/><path d="M8 6c-2 3-1 7 3 10l2-2-2-2-1 1c-1-1-1.5-2-1.5-3l1-1z" fill="var(--orange)"/></svg>
        <span>+6285927461082</span>
      </div>
      <div class="contact__row">
        <svg class="contact__icon" viewBox="0 0 22 22" aria-hidden="true"><rect x="2" y="5" width="18" height="13" rx="2" fill="var(--orange)"/><path d="M3 6l8 6 8-6" fill="none" stroke="#fff" stroke-width="1.8"/></svg>
        <span>tv@korvaladvise.example</span>
      </div>
      <div class="contact__row">
        <svg class="contact__icon" viewBox="0 0 22 22" aria-hidden="true"><circle cx="11" cy="11" r="9" fill="none" stroke="var(--orange)" stroke-width="2"/><ellipse cx="11" cy="11" rx="4" ry="9" fill="none" stroke="var(--orange)" stroke-width="1.5"/><path d="M2 11h18M4 6h14M4 16h14" stroke="var(--orange)" stroke-width="1.5"/></svg>
        <span>www.korvaladvise.example</span>
      </div>
      <div class="contact__address">42 Marlowe Pier, Tarn<br>Vessel Tower, Singapore 073926</div>
    </div>
    <div class="person">
      <div class="person__name">Tomas Velduren</div>
      <div class="person__title">Managing Director</div>
    </div>
  </section>

  <section class="card card--back" aria-label="Card back">
    <div class="company-name">Korval Advise</div>
    <div class="back-url">www.korvaladvise.example</div>
  </section>
</main>
</body>
</html>
```